RW Holloway LLC Business Card - Civil Engineering & Consulting Firm

We need a Business Card that is elegant, and masculine.  It is our Professional Civil Engineering & Consulting Company located in San Antonio TX (Not s construction or builder firm- no gears & no tool images please). We provide civil engineering services including  commercial site plans, grading and drainage plans, utility plans, hydraulics and hydrology, land planning, utility coordination, and other general civil engineering services related to commercial and residential development.
We have 2 existing Logos. We would like to convey reliability, strength, trustworthiness and attention to detail.  Blues and orange tones as per logo We are OK with the use of a darker blue in the mix.  We have 2 logo versions - Full Company Name Logo to go on the back of card, & Small Icon Logo for the front w/ personal Info.

Target Market(s)
Architects, Real Estate Developers, Other Strctural Engineers, Surveyers, General Contractors
Industry/Entity Type
Professional Civil Engineering
Contact Information for Business Card
Name, Position, Address, Cell & Office #, email, and company website
Font styles to use
Other font styles liked:
- Avian
Requirements
Should not have
- No Tools, No Gears, no Cranes, or Construction Equipment.

```html
<!DOCTYPE html>
<html lang="en">
<head>
<meta charset="utf-8">
<title>RW Holloway LLC — Business Card</title>
<link rel="stylesheet" href="https://fonts.googleapis.com/css2?family=Montserrat:wght@400;500;600;700&display=swap">
<style>
  :root {
    --page-bg: #cfcfcf;
    --card-light: #ececed;
    --card-light-2: #f7f7f8;
    --orange: #f0922c;
    --ink: #1d1d1f;
    --back-blue: #7d9fbd;
    --back-grey: #a9988a;
    --back-orange: #e0984f;
    --white: #ffffff;
  }
  * { box-sizing: border-box; margin: 0; padding: 0; }
  html, body {
    width: 1200px; height: 813px; overflow: hidden;
    background: var(--page-bg);
    font-family: "Montserrat", Arial, sans-serif;
  }
  .sheet {
    position: relative; width: 1200px; height: 813px;
    display: flex; align-items: center; justify-content: center; gap: 30px;
  }
  .card {
    position: relative; width: 560px; height: 320px; overflow: hidden;
    box-shadow: 0 6px 18px rgba(0,0,0,.25);
  }

  /* Front */
  .card-front {
    background:
      linear-gradient(125deg, transparent 40%, rgba(255,255,255,.55) 41%, rgba(255,255,255,.2) 70%, transparent 71%),
      linear-gradient(160deg, var(--card-light) 0%, var(--card-light-2) 55%, var(--card-light) 100%);
  }
  .front-brand {
    position: absolute; top: 34px; right: 36px;
    display: flex; align-items: center; gap: 8px;
    font-size: 15px; font-weight: 600; color: var(--orange);
  }
  .front-brand .brand-square { width: 12px; height: 12px; background: var(--orange); }
  .identity { position: absolute; left: 0; top: 122px; display: flex; align-items: stretch; gap: 18px; }
  .identity .accent-bar { width: 22px; background: var(--orange); }
  .identity .person-name {
    font-size: 20px; font-weight: 700; color: var(--orange);
    text-transform: uppercase; letter-spacing: .5px;
  }
  .identity .person-role { font-size: 15px; font-weight: 500; color: var(--ink); margin-top: 4px; }
  .contacts {
    position: absolute; left: 228px; top: 178px;
    font-size: 13px; font-weight: 500; color: var(--ink);
    display: grid; gap: 9px;
  }
  .contacts li { list-style: none; display: flex; align-items: center; gap: 8px; }
  .contacts svg { width: 14px; height: 14px; flex: none; fill: var(--orange); }
  .contacts .address { padding-left: 22px; }

  /* Back */
  .card-back {
    background:
      linear-gradient(120deg, rgba(255,255,255,.08) 0 35%, transparent 35% 60%, rgba(255,255,255,.06) 60%),
      linear-gradient(170deg, var(--back-blue) 0%, var(--back-grey) 45%, var(--back-orange) 100%);
    display: flex; align-items: center; justify-content: center;
  }
  .back-name {
    font-size: 38px; font-weight: 400; color: var(--white);
    letter-spacing: 3px; text-transform: uppercase;
  }
</style>
</head>
<body>
<main class="sheet">
  <section class="card card-front" aria-label="Business card front">
    <div class="front-brand"><span class="brand-square"></span>RW Holloway LLC</div>

    <div class="identity">
      <span class="accent-bar"></span>
      <div>
        <h1 class="person-name">Dara Whitfield</h1>
        <p class="person-role">Co-Founder</p>
      </div>
    </div>

    <ul class="contacts">
      <li class="address">4410 Cedar Ridge Road Suite 210</li>
      <li>
        <svg viewBox="0 0 24 24" aria-hidden="true"><path d="M6.6 10.8a15.1 15.1 0 0 0 6.6 6.6l2.2-2.2a1 1 0 0 1 1-.25 11.4 11.4 0 0 0 3.6.57 1 1 0 0 1 1 1V20a1 1 0 0 1-1 1A17 17 0 0 1 3 4a1 1 0 0 1 1-1h3.5a1 1 0 0 1 1 1c0 1.25.2 2.45.57 3.57a1 1 0 0 1-.25 1z"/></svg>
        555-210-4471
        <svg viewBox="0 0 24 24" aria-hidden="true" style="margin-left:10px"><path d="M6.6 10.8a15.1 15.1 0 0 0 6.6 6.6l2.2-2.2a1 1 0 0 1 1-.25 11.4 11.4 0 0 0 3.6.57 1 1 0 0 1 1 1V20a1 1 0 0 1-1 1A17 17 0 0 1 3 4a1 1 0 0 1 1-1h3.5a1 1 0 0 1 1 1c0 1.25.2 2.45.57 3.57a1 1 0 0 1-.25 1z"/></svg>
        555-210-4472
      </li>
      <li>
        <svg viewBox="0 0 24 24" aria-hidden="true"><path d="M2 5h20v14H2zm2 2v.5l8 5 8-5V7l-8 5z"/></svg>
        info@rwhollowayllc.com
      </li>
      <li>
        <svg viewBox="0 0 24 24" aria-hidden="true"><circle cx="12" cy="12" r="10"/></svg>
        www.hollowaycivil.com
      </li>
    </ul>
  </section>

  <section class="card card-back" aria-label="Business card back">
    <h2 class="back-name">RW Holloway LLC</h2>
  </section>
</main>
</body>
</html>
```